Tovel & Associates - London New Letting and Property Management Company *

Tovel & Associates LTD is a new company based in London, and works with brand new residential property in the city centre.

We are aiming to have 1000 new properties a year.

We are looking for something modern and minimalistic :
Logo ,Monogram, Paper Head and Business Card.

Target Market(s)

Internation landlords

Industry/Entity Type

Real Estate

Logo Text

Tovel & Associates

Colors

Designer to choose colors to be used in the design.

Requirements
Nice to have
• A particular monogram with "TA"
Should not have
• Little House over the logo

```html
<!DOCTYPE html>
<html lang="en">
<head>
<meta charset="UTF-8">
<title>Tovel &amp; Associates – Business Card</title>
<link href="https://fonts.googleapis.com/css2?family=Montserrat:wght@700&family=Work+Sans:wght@400;500&display=swap" rel="stylesheet">
<style>
  :root {
    --bg: #1b1b1c;
    --card: #232425;
    --card-edge: #2c2d2f;
    --brand: #215f8e;
    --accent: #1ea3e6;
    --text: #f1f3f5;
    --muted: #c9ced3;
  }
  * { margin: 0; padding: 0; box-sizing: border-box; }
  html, body {
    width: 1200px; height: 900px; overflow: hidden;
    background: var(--bg);
  }
  .stage {
    width: 1200px; height: 900px;
    display: flex; flex-direction: column;
    align-items: center; justify-content: center;
    gap: 36px;
  }
  .card {
    position: relative;
    width: 720px; height: 400px;
    background: linear-gradient(135deg, var(--card) 0%, var(--card-edge) 100%);
    box-shadow: 0 10px 30px rgba(0,0,0,.55);
  }
  .wordmark {
    font-family: "Montserrat", sans-serif;
    font-weight: 700;
    color: var(--brand);
    letter-spacing: 0.12em;
    text-transform: uppercase;
    display: flex; align-items: center; gap: 10px;
    white-space: nowrap;
  }
  .wordmark__square {
    width: 14px; height: 14px; background: var(--brand);
  }
  .card--front .wordmark {
    position: absolute; left: 50%; top: 50%;
    transform: translate(-50%, -50%);
    font-size: 26px;
  }
  .card--back .wordmark {
    position: absolute; right: 44px; top: 96px;
    font-size: 17px;
  }
  .person {
    position: absolute; left: 60px; top: 150px;
    font-family: "Work Sans", sans-serif;
  }
  .person__name {
    font-family: "Montserrat", sans-serif;
    font-weight: 700;
    font-size: 30px; letter-spacing: 0.04em;
    color: var(--accent);
    text-transform: uppercase;
  }
  .person__role {
    font-size: 18px; color: var(--text); margin-top: 2px;
  }
  .divider {
    position: absolute; left: 56px; right: 60px; top: 236px;
    height: 2px; background: var(--accent);
  }
  .contacts {
    position: absolute; left: 56px; top: 262px;
    list-style: none;
    font-family: "Work Sans", sans-serif;
    font-size: 18px; color: var(--text);
    display: flex; flex-direction: column; gap: 6px;
  }
  .contacts__item { display: flex; align-items: center; gap: 12px; }
  .contacts__icon { width: 13px; height: 13px; flex: none; }
  .address {
    position: absolute; right: 60px; bottom: 40px;
    font-family: "Work Sans", sans-serif;
    font-size: 20px; line-height: 1.35; color: var(--text);
    font-style: normal;
  }
</style>
</head>
<body>
<main class="stage">
  <section class="card card--front" aria-label="Card front">
    <div class="wordmark"><span class="wordmark__square"></span>Tovel &amp; Associates</div>
  </section>

  <section class="card card--back" aria-label="Card back">
    <div class="wordmark"><span class="wordmark__square"></span>Tovel &amp; Associates</div>

    <div class="person">
      <h1 class="person__name">Daniel Wrexham</h1>
      <p class="person__role">Director</p>
    </div>

    <div class="divider"></div>

    <ul class="contacts">
      <li class="contacts__item">
        <svg class="contacts__icon" viewBox="0 0 16 16" aria-hidden="true"><path d="M4 1c1 0 2 3 2 4s-1 1-1 2 2 4 4 4c1 0 1-1 2-1s4 1 4 2-1 3-3 3C6 15 1 10 1 4c0-2 2-3 3-3z" fill="var(--accent)"/></svg>
        +44 20 7946 0183
      </li>
      <li class="contacts__item">
        <svg class="contacts__icon" viewBox="0 0 16 16" aria-hidden="true"><rect x="1" y="3" width="14" height="10" fill="none" stroke="var(--accent)" stroke-width="1.6"/><path d="M1 3l7 6 7-6" fill="none" stroke="var(--accent)" stroke-width="1.6"/></svg>
        info@tovelassociates.com
      </li>
      <li class="contacts__item">
        <svg class="contacts__icon" viewBox="0 0 16 16" aria-hidden="true"><circle cx="8" cy="8" r="6.5" fill="none" stroke="var(--accent)" stroke-width="1.4"/><ellipse cx="8" cy="8" rx="3" ry="6.5" fill="none" stroke="var(--accent)" stroke-width="1.2"/><path d="M1.5 8h13" stroke="var(--accent)" stroke-width="1.2"/></svg>
        www.tovelassociates.com
      </li>
    </ul>

    <address class="address">18 Carlow Crescent<br>London EC2A 4NE</address>
  </section>
</main>
</body>
</html>
```